A start-up named "lumerova" - a clinical research organization needs a new PowerPoint design

We need a new PowerPoint Design (incl. business card and stationery design) for an early-stage start-up named "lumerova" seeking to build an ecosystem/ strategic partner alliances or consortium of committed and active collaborators to guide important components of the clinical trial.

Our ultimate goal is to avoid false neutrals – therapies that have not been and may never be evaluated in clinical trials due to the costs and/ or complexity.

The final design should highlight our patient-centric approach, innovative study design supported with the novel AI platform to make a stronger impact on patient lives.

Please see the attached brief for more details.
Updates

Requesting the proposals on color-coding, business-card designs, clinical research visuals, and icons as well as stationery design.

Target Market(s)

Pharma/ Biotech Executives
Medical Institutions
Clinical Trial Participants (Patients)

Colors
e34398

Requirements
Must have
• Use the Color Version of purple/ magenta logo

```html
<!DOCTYPE html>
<html lang="en">
<head>
<meta charset="utf-8">
<title>lumerova business card</title>
<link rel="stylesheet" href="https://fonts.googleapis.com/css2?family=Open+Sans:wght@400;600;700&display=swap">
<style>
  :root {
    --magenta: #b3206a;
    --magenta-light: #bf3079;
    --magenta-deep: #a51a60;
    --ink: #1a1a1a;
    --paper: #ffffff;
    --faint: #f1f1f2;
    --backdrop: #e9e9eb;
  }
  * { margin: 0; padding: 0; box-sizing: border-box; }
  html, body {
    width: 1200px; height: 1200px; overflow: hidden;
    background: var(--backdrop);
    font-family: "Open Sans", Arial, sans-serif;
  }
  .sheet {
    position: relative; width: 1200px; height: 1200px;
    display: flex; flex-direction: column; align-items: center; justify-content: center; gap: 60px;
  }
  .card {
    position: relative; width: 860px; height: 520px; overflow: hidden;
    box-shadow: 0 6px 24px rgba(0,0,0,.12);
  }

  /* Front */
  .card-front { background: var(--magenta); }
  .front-pattern {
    position: absolute; inset: 0;
    background: linear-gradient(135deg, var(--magenta-light) 0%, var(--magenta) 50%, var(--magenta-deep) 100%);
  }
  .front-brand {
    position: absolute; left: 0; right: 0; top: 200px;
    display: flex; align-items: center; justify-content: center; gap: 18px;
    color: var(--paper); font-weight: 700; font-size: 92px; line-height: 1; letter-spacing: -1px;
  }
  .front-brand .brand-square { width: 40px; height: 40px; background: var(--paper); margin-top: 22px; }

  /* Back */
  .card-back { background: var(--paper); color: var(--ink); }
  .back-pattern {
    position: absolute; left: 200px; top: 80px; width: 340px; height: 300px;
    border-radius: 24px;
    background: linear-gradient(160deg, var(--faint) 0%, #f6f6f7 60%, var(--paper) 100%);
  }
  .name-rule-top { position: absolute; left: 0; top: 40px; width: 62px; height: 2px; background: var(--magenta); opacity: .6; }
  .name-rule { position: absolute; left: 0; top: 58px; width: 62px; height: 3px; background: var(--magenta); }
  .holder { position: absolute; left: 78px; top: 38px; }
  .holder-name { font-size: 32px; font-weight: 700; line-height: 1.1; }
  .holder-role { font-size: 16px; color: var(--magenta); margin-top: 4px; }
  .back-brand {
    position: absolute; left: 60px; top: 218px;
    display: flex; align-items: center; gap: 12px;
    color: var(--magenta); font-weight: 700; font-size: 50px; line-height: 1; letter-spacing: -.5px;
  }
  .back-brand .brand-square { width: 22px; height: 22px; background: var(--magenta); margin-top: 12px; }

  .contact { position: absolute; font-size: 16px; line-height: 1.45; font-weight: 600; }
  .contact-row { display: flex; align-items: flex-start; gap: 10px; }
  .icon { width: 18px; height: 18px; flex: none; margin-top: 3px; fill: var(--magenta); }
  .address { left: 560px; top: 150px; }
  .online { left: 520px; top: 290px; }
  .phones { left: 470px; top: 380px; }

  .footer-band { position: absolute; left: 0; right: 0; bottom: 22px; height: 4px; background: var(--magenta); }
</style>
</head>
<body>
<main class="sheet">
  <section class="card card-front" aria-label="Card front">
    <div class="front-pattern" role="img" aria-label="Tonal magenta square-block brand pattern"></div>
    <div class="front-brand"><span class="brand-name">lumerova</span><span class="brand-square"></span></div>
  </section>

  <section class="card card-back" aria-label="Card back">
    <div class="back-pattern" role="img" aria-label="Faint grey square-block brand pattern"></div>
    <span class="name-rule-top"></span>
    <span class="name-rule"></span>
    <div class="holder">
      <p class="holder-name">Name Surname, PhD</p>
      <p class="holder-role">Managing Partner</p>
    </div>
    <div class="back-brand"><span class="brand-name">lumerova</span><span class="brand-square"></span></div>

    <div class="contact address">
      <div class="contact-row">
        <svg class="icon" viewBox="0 0 24 24" aria-hidden="true"><path d="M12 2a7 7 0 0 0-7 7c0 5 7 13 7 13s7-8 7-13a7 7 0 0 0-7-7zm0 9.5A2.5 2.5 0 1 1 12 6.5a2.5 2.5 0 0 1 0 5z"/></svg>
        <p>Lumerova GmbH<br>Street name 1<br>9999 City name<br>Switzerland</p>
      </div>
    </div>

    <div class="contact online">
      <div class="contact-row">
        <svg class="icon" viewBox="0 0 24 24" aria-hidden="true"><path d="M2 5h20v14H2z M2 5l10 8 10-8" stroke="#fff" stroke-width="1.5"/></svg>
        <p>name.surname@lumerova.ch</p>
      </div>
      <div class="contact-row">
        <svg class="icon" viewBox="0 0 24 24" aria-hidden="true"><circle cx="12" cy="12" r="10"/><path d="M2 12h20M12 2c3 3 3 17 0 20M12 2c-3 3-3 17 0 20" stroke="#fff" stroke-width="1.4" fill="none"/></svg>
        <p>www.lumerova.ch</p>
      </div>
    </div>

    <div class="contact phones">
      <p>Office: +41 (0)44 218 70 10</p>
      <p>Phone: +41 (0)44 218 70 24</p>
      <p>Mobile: +41 (0)79 503 16 48</p>
      <p>Fax: +41 (0)44 218 70 11</p>
    </div>

    <div class="footer-band"></div>
  </section>
</main>
</body>
</html>
```